Business Cards Needed for Innovative Healthcare Marketing Company

We are a marketing company focused on healthcare. Our company is all about rebranding yourself renewing your image and generating results. The phoenix stands for "reborn" or "rising" which we provide new brands for our clients we take their old brands and renew it with creativity and innovation. I am looking for a business card with color dimension. I have attached an example of a card I think has the look and feel of what I am trying to accomplish. I like that the card example has black and grey font colors, I like the font placement and the small logo, I really like the use of the colors on the right those are the colors of my logo. My logo is phoenix so maybe incorporating flames similar to that design. I would like the back a solid color maybe red with an opaque version of the logo and website. As a marketing company I am always open to creative liberty!

Target Market(s)

Doctors and business professionals.

Industry/Entity Type

Marketing

Contact Information for Business Card

Valcorne Health Care Marketing
Marla Tenwick- CEO
#(512)638-2974
email-marla@valcorne.com
website- valcorne.com

Font styles to use
Sans Serif

Colors
ec1f27
f37122
ffc214
fbed22
fbf289
f04a50

Requirements
Must have
• The logo and required information
Nice to have
• icons by the information
Should not have
• child like font

```html
<!DOCTYPE html>
<html lang="en">
<head>
<meta charset="utf-8">
<title>Valcorne Health Care Marketing – Business Card</title>
<link rel="stylesheet" href="https://fonts.googleapis.com/css2?family=Open+Sans:wght@300;400;700&display=swap">
<style>
  :root {
    --page: #ece9e6;
    --card-white: #ffffff;
    --brand-red: #9b1b1e;
    --flame-orange: #f7941d;
    --flame-deep: #a81f1c;
    --back-orange: #f39021;
    --back-red: #b2241f;
    --ink-light: #ffffff;
  }
  * { box-sizing: border-box; margin: 0; padding: 0; }
  html, body {
    width: 1200px; height: 900px; overflow: hidden;
    background: var(--page);
    font-family: "Open Sans", Arial, sans-serif;
  }
  .canvas { position: relative; width: 1200px; height: 900px; }

  .card { position: absolute; overflow: hidden; box-shadow: 0 6px 18px rgba(0,0,0,.18); }

  /* Front */
  .card--front { left: 78px; top: 34px; width: 588px; height: 364px; background: var(--card-white); }
  .brand { position: absolute; left: 37px; top: 40px; display: flex; align-items: flex-start; gap: 18px; }
  .brand__dot { width: 64px; height: 64px; border-radius: 50%; background: linear-gradient(180deg, var(--flame-deep), var(--flame-orange)); margin-top: 6px; }
  .brand__text { color: var(--brand-red); font-weight: 300; }
  .brand__name { font-size: 50px; line-height: 56px; letter-spacing: 1px; }
  .brand__rule { height: 1px; background: var(--brand-red); margin: 10px 0 6px; width: 252px; }
  .brand__tagline { font-size: 18.5px; letter-spacing: 1.2px; line-height: 24px; }

  .contact-band {
    position: absolute; left: 0; top: 168px; width: 588px; height: 196px;
    background: linear-gradient(180deg, var(--flame-orange) 0%, #e5661f 45%, var(--flame-deep) 100%);
    clip-path: polygon(0 0, 100% 4px, 100% 100%, 0 100%);
  }
  .contact-band__mark {
    position: absolute; right: 6px; top: -4px; width: 160px; height: 196px;
    background: var(--card-white); border-radius: 80px 80px 0 60px;
  }
  .contact-band__mark-fill {
    position: absolute; inset: 8px; border-radius: 72px 72px 0 52px;
    background: linear-gradient(180deg, var(--flame-deep), var(--flame-orange));
    opacity: .85;
  }
  .person { position: absolute; left: 30px; top: 22px; color: var(--ink-light); }
  .person__name { font-size: 21px; font-weight: 700; line-height: 28px; }
  .person__role { font-size: 14px; line-height: 20px; }
  .contact-list { position: absolute; left: 30px; top: 96px; list-style: none; color: var(--ink-light); font-size: 14.5px; }
  .contact-list li { display: flex; align-items: center; gap: 12px; height: 25px; }
  .contact-list svg { width: 12px; height: 12px; fill: var(--ink-light); }

  /* Back */
  .card--back {
    left: 389px; top: 505px; width: 565px; height: 352px;
    background: linear-gradient(100deg, var(--back-orange) 0%, #d5571f 45%, var(--back-red) 100%);
  }
  .back__mark {
    position: absolute; left: 10px; top: 10px; width: 290px; height: 330px;
    border-radius: 145px 145px 40px 40px;
    background: linear-gradient(180deg, rgba(160,30,28,.45), rgba(250,170,40,.35));
  }
  .back__web {
    position: absolute; left: 269px; top: 287px;
    color: var(--ink-light); font-size: 15px; letter-spacing: 5px; font-weight: 400;
  }
</style>
</head>
<body>
<main class="canvas">

  <section class="card card--front" aria-label="Business card front">
    <div class="brand">
      <span class="brand__dot"></span>
      <div class="brand__text">
        <div class="brand__name">VALCORNE</div>
        <div class="brand__rule"></div>
        <div class="brand__tagline">HEALTH CARE MARKETING</div>
      </div>
    </div>

    <div class="contact-band">
      <div class="person">
        <div class="person__name">Marla Tenwick</div>
        <div class="person__role">CEO</div>
      </div>
      <ul class="contact-list">
        <li><svg viewBox="0 0 24 24"><path d="M6.6 10.8a15.1 15.1 0 0 0 6.6 6.6l2.2-2.2c.3-.3.7-.4 1-.2 1.1.4 2.3.6 3.6.6.6 0 1 .4 1 1V20c0 .6-.4 1-1 1A17 17 0 0 1 3 4c0-.6.4-1 1-1h3.5c.6 0 1 .4 1 1 0 1.3.2 2.5.6 3.6.1.3 0 .7-.2 1z"/></svg>(512)638-2974</li>
        <li><svg viewBox="0 0 24 24"><path d="M2 5h20v14H2z M2 5l10 8 10-8" stroke="#e5661f" stroke-width="2"/></svg>marla@valcorne.com</li>
        <li><svg viewBox="0 0 24 24"><circle cx="12" cy="12" r="11"/></svg>www.valcorne.com</li>
      </ul>
      <div class="contact-band__mark">
        <div class="contact-band__mark-fill" role="img" aria-label="Brand emblem area in flame tones"></div>
      </div>
    </div>
  </section>

  <section class="card card--back" aria-label="Business card back">
    <div class="back__mark" role="img" aria-label="Faint brand emblem area"></div>
    <div class="back__web">www.valcorne.com</div>
  </section>

</main>
</body>
</html>
```